Website for new child psychology practice

New clinical psychology practice in NSW Australia, specialising in work with children, adolescents and families. I would like to feature the colours in the logo, which was recently designed by pixelharbor designer Odette.
I am seeking a professional looking page, which is easy to navigate and is colourful and playful but not childish.
Target Market(s)
Parents and professionals
Industry/Entity Type
Health
Coding
Coded - Design and coding required
Number of Pages Required
1 page
Font styles to use
Serif
Requirements
Must have
- Pages for 'About us' 'Services' 'Fees and information' 'Contact us'
Should not have
- Childish stock photos

```html
<!DOCTYPE html>
<html lang="en">
<head>
<meta charset="utf-8">
<title>Dr Clara Bennett – Clinical Psychologist</title>
<link href="https://fonts.googleapis.com/css2?family=Cinzel:wght@400;500;600&family=Poppins:wght@400;500&display=swap" rel="stylesheet">
<style>
:root{
  --plum:#7b1f5e;
  --coral:#ef5a4c;
  --magenta:#a0218f;
  --red:#d8262b;
  --sand:#fbddb0;
  --ink:#2b2b2b;
  --white:#ffffff;
  --serif:'Cinzel', serif;
  --sans:'Poppins', sans-serif;
}
*{margin:0;padding:0;box-sizing:border-box}
html,body{width:1200px;height:3098px;overflow:hidden;background:var(--white)}
body{position:relative;font-family:var(--sans);color:var(--ink)}
.abs{position:absolute}
.header{left:0;top:0;width:1200px;height:100px}
.brand{left:75px;top:30px;display:flex;align-items:center;gap:10px;font-family:var(--serif);font-size:30px;font-weight:500;color:var(--plum)}
.brand-dot{width:34px;height:34px;border-radius:50%;background:var(--magenta)}
.nav{right:72px;top:43px;display:flex;gap:42px;font-family:var(--serif);font-size:16px;letter-spacing:1px;color:var(--ink)}
.hero{left:0;top:100px;width:1200px;height:618px;background:linear-gradient(120deg,#4d4845 0%,#7d7872 45%,#58504a 100%)}
.hero-text{left:0;top:292px;width:1200px;text-align:center;color:var(--white);font-family:var(--serif)}
.hero-text .small{font-size:42px;line-height:48px}
.hero-text .big{font-size:66px;line-height:66px;font-weight:500}
.hero-text .sub{font-size:36px;line-height:44px}
.btn{display:flex;align-items:center;justify-content:center;background:var(--red);color:var(--white);border-radius:30px;font-family:var(--serif);font-size:16px;letter-spacing:1px}
.hero .btn{position:absolute;left:459px;top:360px;width:281px;height:53px}
.bloom{border-radius:50%;background:radial-gradient(circle,#f6a24a 0%,#c6368f 60%,#7b1f5e 100%);opacity:.85}
.photo{border-radius:50%;border:6px solid var(--white)}
.h2{font-family:var(--serif);font-size:36px;font-weight:500;color:var(--ink);letter-spacing:1px}
.h2 span{color:var(--plum)}
.copy{font-size:15px;line-height:30.4px;color:var(--ink)}
.band{left:0;width:1200px;background:var(--sand);border-radius:44px}
.card{top:1449px;width:328px;height:258px;border-radius:32px;color:var(--white);text-align:center}
.card .icon{width:70px;height:70px;margin:22px auto 0;border:2px solid var(--white);border-radius:14px;opacity:.9}
.card h3{font-family:var(--serif);font-weight:500;font-size:26px;margin-top:18px;letter-spacing:1px}
.card p{font-size:14px;line-height:24px;margin-top:8px;padding:0 18px}
.field{background:var(--white);border-radius:26px;font-size:14px;padding:14px 20px;color:var(--ink)}
.footnav{left:74px;top:2994px;display:flex;gap:42px;font-family:var(--serif);font-size:16px;letter-spacing:1px}
.social{left:958px;top:3010px;display:flex;gap:14px}
.social i{display:block;width:22px;height:22px;border-radius:50%;background:var(--ink)}
</style>
</head>
<body>
<header class="abs header">
  <div class="abs brand"><span class="brand-dot"></span>Dr Clara Bennett</div>
  <nav class="abs nav"><span>About us</span><span>Services</span><span>Fees and information</span><span>Contact us</span></nav>
</header>

<section class="abs hero" role="img" aria-label="Photo of a therapy session with two women talking on a sofa">
  <div class="abs hero-text" style="top:192px">
    <div class="small">Welcome to</div>
    <div class="big">Dr Clara Bennett</div>
    <div class="sub">Clinical Psychologist</div>
  </div>
  <div class="btn">Request Appointment</div>
</section>

<section class="about">
  <div class="abs bloom" style="left:60px;top:766px;width:440px;height:470px" role="img" aria-label="Colourful petal cluster decoration"></div>
  <div class="abs photo" style="left:104px;top:810px;width:390px;height:390px;background:linear-gradient(140deg,#e6e0d6,#c8bba8)" role="img" aria-label="Portrait of the psychologist seated with a clipboard"></div>
  <h2 class="abs h2" style="left:616px;top:826px">About <span>Dr. Clara Bennett</span></h2>
  <p class="abs copy" style="left:616px;top:883px;width:520px">Sed ut perspiciatis unde omnis iste natus error sit<br>voluptatem accusantium doloremque laudantium, totam rem<br>aperiam, eaque ipsa quae ab illo inventore veritatis et quasi<br>architecto beatae vitae dicta sunt explicabo. Nemo enim ipsam<br>voluptatem quia voluptas sit aspernatur aut odit aut fugit, sed quia<br>consequuntur magni dolores eos qui ratione voluptatem<br>sequi nesciunt</p>
  <div class="abs btn" style="left:616px;top:1122px;width:178px;height:53px">Read More</div>
</section>

<section class="abs band" style="top:1281px;height:494px"></section>
<h2 class="abs h2" style="left:0;top:1336px;width:1200px;text-align:center">Our <span>Services</span></h2>
<p class="abs" style="left:0;top:1393px;width:1200px;text-align:center;font-size:15px">Sed ut perspiciatis unde omnis iste natus error sit voluptatem accusantium doloremque laudantium.</p>
<div class="abs card" style="left:75px;background:var(--plum)"><div class="icon"></div><h3>Children</h3><p>Sed ut perspiciatis unde omnis iste natus error sit voluptatem accusantium doloremque quasi architecto beatae vitae dicta sunt explicabo.</p></div>
<div class="abs card" style="left:436px;background:var(--coral)"><div class="icon"></div><h3>Adolescents</h3><p>Sed ut perspiciatis unde omnis iste natus error sit voluptatem accusantium doloremque quasi architecto beatae vitae dicta sunt explicabo.</p></div>
<div class="abs card" style="left:798px;background:var(--magenta)"><div class="icon"></div><h3>Families</h3><p>Sed ut perspiciatis unde omnis iste natus error sit voluptatem accusantium doloremque quasi architecto beatae vitae dicta sunt explicabo.</p></div>

<section class="fees">
  <h2 class="abs h2" style="left:78px;top:1886px">Fees And <span>Information</span></h2>
  <p class="abs copy" style="left:75px;top:1943px;width:540px">Sed ut perspiciatis unde omnis iste natus error sit<br>voluptatem accusantium doloremque laudantium, totam rem<br>aperiam, eaque ipsa quae ab illo inventore veritatis et quasi<br>architecto beatae vitae dicta sunt explicabo. Nemo enim ipsam<br>voluptatem quia voluptas sit aspernatur aut odit aut fugit, sed quia<br>consequuntur magni dolores eos qui ratione voluptatem<br>sequi nesciunt</p>
  <div class="abs btn" style="left:75px;top:2183px;width:178px;height:53px">Read More</div>
  <div class="abs bloom" style="left:720px;top:1812px;width:470px;height:505px" role="img" aria-label="Colourful petal cluster decoration"></div>
  <div class="abs photo" style="left:734px;top:1870px;width:390px;height:390px;background:linear-gradient(140deg,#e9ecef,#b9c3cc)" role="img" aria-label="Online video consultation on a laptop"></div>
</section>

<section class="abs band" style="top:2369px;height:573px"></section>
<h2 class="abs h2" style="left:0;top:2430px;width:1200px;text-align:center">Contact <span>Us</span></h2>
<p class="abs" style="left:70px;top:2492px;width:1060px;text-align:center;font-size:15px;line-height:27px">Sed ut perspiciatis unde omnis iste natus error sit voluptatem accusantium doloremque laudantium, totam rem aperiam, eaque ipsa quae ab illo inventore veritatis et quasi architecto beatae vitae dicta sunt explicabo.</p>
<div class="abs field" style="left:254px;top:2571px;width:338px;height:48px">Enter Name</div>
<div class="abs field" style="left:608px;top:2571px;width:337px;height:48px">Email Address</div>
<div class="abs field" style="left:254px;top:2633px;width:338px;height:48px">Phone No</div>
<div class="abs field" style="left:608px;top:2633px;width:337px;height:48px">Subject</div>
<div class="abs field" style="left:254px;top:2694px;width:691px;height:111px">Message</div>
<div class="abs btn" style="left:511px;top:2820px;width:177px;height:52px">Submit</div>

<footer>
  <nav class="abs footnav"><span>About us</span><span>Services</span><span>Fees and information</span><span>Contact us</span></nav>
  <p class="abs" style="left:74px;top:3034px;font-size:12px">© Copyright 2024.Company Name.&nbsp; All Right Reserved</p>
  <div class="abs social" aria-label="Social links"><i></i><i></i><i></i><i></i><i></i></div>
</footer>
</body>
</html>
```